Quote Cards With KB May 2025 for Instagram

I would like to put these quotes over one of the pictures attached; Instagram (new size: 4:5 (1080 x 1350 pixels) One Quote per picture, and I want the quote to be bold or easy to read as well. I provided a few reference graphics that I really like as examples below. In very small letters at the bottom add @KBHarlowOnline

All of the pictures are attached; you can pick any photo and add one quote to it; but no stock photography

```html
<!DOCTYPE html>
<html lang="en">
<head>
<meta charset="utf-8">
<title>Quote Card – Hormones</title>
<link href="https://fonts.googleapis.com/css2?family=Crimson+Pro:wght@500&family=Poppins:wght@600&display=swap" rel="stylesheet">
<style>
  :root {
    --hot-pink: #ff3a9f;
    --magenta: #e24fc0;
    --violet: #6a3a8c;
    --arena-dark: #2b2238;
    --court-wood: #c9a07a;
    --court-orange: #f7a12a;
    --white: #ffffff;
  }
  * { margin: 0; padding: 0; box-sizing: border-box; }
  html, body {
    width: 960px;
    height: 1200px;
    overflow: hidden;
    background: var(--white);
  }
  .card {
    position: relative;
    width: 960px;
    height: 1200px;
    overflow: hidden;
  }
  .photo {
    position: absolute;
    inset: 0;
    background:
      linear-gradient(180deg, var(--arena-dark) 0%, var(--violet) 38%, var(--court-wood) 62%, #b88a64 100%);
  }
  .tint {
    position: absolute;
    inset: 0;
    background:
      linear-gradient(100deg, rgba(255,58,159,0) 28%, rgba(226,79,192,0.55) 45%, var(--hot-pink) 68%),
      linear-gradient(200deg, rgba(255,58,159,0) 55%, rgba(247,161,42,0.75) 88%);
  }
  .frame {
    position: absolute;
    inset: 0;
    width: 960px;
    height: 1200px;
  }
  .quote {
    position: absolute;
    left: 440px;
    width: 450px;
    text-align: center;
    color: var(--white);
    font-family: "Crimson Pro", Georgia, serif;
    font-weight: 500;
    font-size: 62px;
    line-height: 75px;
    letter-spacing: -0.3px;
  }
  .quote--headline { top: 232px; }
  .quote--call { top: 680px; }
  .handle {
    position: absolute;
    left: 0;
    width: 960px;
    top: 1121px;
    text-align: center;
    color: var(--white);
    font-family: "Poppins", Arial, sans-serif;
    font-weight: 600;
    font-size: 31px;
    line-height: 38px;
  }
</style>
</head>
<body>
  <main class="card">
    <div class="photo" role="img" aria-label="Photo of a smiling woman with long dark hair in a sparkly brown turtleneck and black jeans, standing on a basketball court inside an arena"></div>
    <div class="tint"></div>

    <svg class="frame" viewBox="0 0 960 1200" aria-hidden="true">
      <path d="M283 1146 H70 A36 36 0 0 1 34 1110 V76 A36 36 0 0 1 70 40 H893 A36 36 0 0 1 929 76 V1110 A36 36 0 0 1 893 1146 H673"
            fill="none" stroke="var(--white)" stroke-width="3"/>
    </svg>

    <p class="quote quote--headline">Your belly<br>isn’t fat…<br>it’s hormonal.<br>And here’s<br>how to fix it.</p>
    <p class="quote quote--call">Comment<br>HORMONES<br>ifnothing is<br>working.</p>

    <p class="handle">@KBHarlowOnline</p>
  </main>
</body>
</html>
```